Website Redesign for MarrowArc.co.za – Bold, Modern & Professional Tattoo Supply Store (B2B ...

We’re looking for a skilled and creative web designer to redesign MarrowArc.co.za, a leading tattoo equipment and supplies store based in South Africa. The business serves both B2B (tattoo studios, artists, wholesalers) and B2C (individual customers) markets.

The current website is outdated and lacks the modern, edgy look that reflects the tattoo industry. We want a fresh, bold, and professional design that appeals to both professional artists and retail customers — combining trust, style, and functionality.

About the Business:
Marrow Arc supplies a wide range of tattoo-related products, including machines, needles, inks, hygiene supplies, and accessories. The company is well-established in the South African market and serves both individual tattoo artists and studios, as well as end customers looking for quality equipment.

The website must reflect the creative, bold, and artistic nature of the tattoo industry, while still being easy to navigate, fast, and conversion-focused.

What We’re Looking For:
A bold, modern design with a clear structure
Strong visual identity that reflects the tattoo culture — edgy, artistic, but still clean and professional
A layout that works for both B2B and B2C audiences
Clear product presentation and strong CTAs (Buy Now, Request Quote, Contact, etc.)
Fully responsive design (desktop + mobile)
Easy-to-navigate product categories and filters
Space for featured products, promotions, and artist-focused content
Integration of trust elements (payment icons, reviews, certifications, etc.)

Pages We Need Designed:
Homepage
Product detail page

Inspiration / Style Direction:
We’re looking for something with a strong personality, inspired by tattoo culture, but still clean and user-friendly. Think:

Dark theme with bold highlights (but open to light themes if well executed)
High-quality visuals and product imagery

Examples for inspiration:
GrimQuill.co.uk
Wexley RPN
Corvane Needle Supply
Brisk Tallow

Deliverables:
Full desktop and mobile designs (Figma, XD, or PSD)
All design source files
Fonts, icons, and assets used
Clearly labeled layers and organized files
Ready for development handoff

Target Market(s)

MarrowArc.co.za targets both B2B and B2C customers in South Africa: B2B: Professional tattoo artists, studios, and wholesalers looking for high-quality, reliable equipment and bulk pricing. B2C: Individual customers, hobbyists, and beginners seeking safe, affordable tattoo supplies with guidance and support. The site should appeal to both experienced professionals and newcomers, combining a bold, authentic tattoo vibe with a clean, user-friendly shopping experience.

Industry/Entity Type

Tattoo Equipment & Supplies – E-commerce (B2B & B2C)

Number of Pages Required

2 page

Requirements
Must have
• Responsive design, bold tattoo-inspired visual style, clear navigation for B2B & B2C, strong product presentation, clear call-to-actions, trust elements (reviews, badges, payment icons), category filters & search, dedicated B2B/wholesale info page, speed-optimized layout, easy access to contact & support.
Should not have
• Overly complex animations, cluttered layout, generic stock images, too many fonts or colors, hidden navigation, auto-play videos or sounds, outdated visual styles, low-quality product images, confusing checkout process, unnecessary pop-ups.

```html
<!DOCTYPE html>
<html lang="en">
<head>
<meta charset="utf-8">
<title>Marrow Arc – Premium Tattoo Equipment</title>
<link href="https://fonts.googleapis.com/css2?family=Russo+One&family=Poppins:wght@400;500;600;700&display=swap" rel="stylesheet">
<style>
:root{
  --red:#c8141c;
  --red-deep:#8e0d10;
  --wine:#4a0a0d;
  --yellow:#f2b705;
  --ink:#0c0c0c;
  --panel:#141414;
  --line:#2c2c2c;
  --white:#ffffff;
  --muted:#b9b9b9;
  --ph:#3a3a3a;
  --display:"Russo One", sans-serif;
  --body:"Poppins", sans-serif;
}
*{box-sizing:border-box;margin:0;padding:0}
html,body{width:1200px;height:5396px;overflow:hidden}
body{background:var(--ink);color:var(--white);font-family:var(--body);position:relative}
section,header,footer,.topbar{position:absolute;left:0;width:1200px;overflow:hidden}
.abs{position:absolute}
.btn{position:absolute;display:flex;align-items:center;justify-content:center;font-family:var(--body);font-weight:600;font-size:12px;text-transform:uppercase;letter-spacing:.3px}
.btn-red{background:var(--red);color:var(--white)}
.btn-white{background:var(--white);color:var(--red)}
.ph{position:absolute}
.h-sec{position:absolute;font-family:var(--display);font-size:30px;letter-spacing:1px;text-transform:uppercase}
.h-sec .y{color:var(--yellow)}
.sub{position:absolute;font-size:13px;color:var(--muted)}

/* top bar */
.topbar{top:0;height:27px;background:var(--red-deep);display:flex;align-items:center;justify-content:center;font-size:11px;gap:150px}
.topbar b{font-weight:600}
/* header */
.site-header{top:27px;height:71px;background:#0b0b0b}
.logo{position:absolute;font-family:var(--display);color:var(--white);letter-spacing:1px;display:flex;align-items:center;gap:8px}
.logo i{display:block;width:12px;height:12px;background:var(--red)}
.nav{position:absolute;left:368px;top:27px;display:flex;gap:18px;font-size:12px;font-weight:500}
.icons{position:absolute;left:985px;top:21px;display:flex;gap:12px}
.icons span{width:24px;height:24px;border:1.5px solid #ddd;border-radius:50%;display:flex;align-items:center;justify-content:center}
/* hero */
.hero{top:98px;height:578px;background:linear-gradient(90deg,#121212,#1d1d1d)}
.hero-photo{left:540px;top:0;width:660px;height:578px;background:linear-gradient(135deg,#5a1420 0%,#2a0c14 45%,#120a10 100%);clip-path:polygon(120px 0,660px 0,660px 578px,0 578px,40px 430px,80px 250px)}
.hero h1{position:absolute;left:124px;top:138px;font-family:var(--display);font-size:46px;line-height:61px;font-weight:400}
.hero h1 .y{color:var(--yellow)}
.hero p{position:absolute;left:124px;top:332px;width:470px;font-size:13px;line-height:21px;color:#d5d5d5}
/* categories */
.cats{top:676px;height:245px;background:linear-gradient(180deg,#3c0709,#5a0c10 60%,#3a0708)}
.cat{position:absolute;top:67px;width:160px;text-align:center}
.cat .c{width:105px;height:105px;margin:0 auto;border-radius:50%;background:#f4f4f4;border:4px solid #2a0606;display:flex;align-items:center;justify-content:center}
.cat .c div{width:60px;height:60px;border-radius:50%;background:linear-gradient(160deg,#cfcfcf,#7a7a7a)}
.cat p{margin-top:16px;font-size:14px;color:var(--yellow);font-weight:500}
.cat.dim{opacity:.45}
/* featured */
.featured{top:921px;height:712px;background:#0e0e0e}
.fcard{position:absolute;top:136px;width:300px}
.fcard .img{height:367px;background:linear-gradient(160deg,#4a4a4a,#2c2c2c);position:relative}
.fcard .img .heart{position:absolute;right:12px;top:12px;width:24px;height:24px;border-radius:50%;background:#1a1a1a;border:1px solid #666}
.fcard h3{margin-top:18px;font-size:17px;font-weight:600;line-height:25px}
.fcard p{margin-top:8px;font-size:11px;line-height:17px;color:var(--muted)}
.fcard .btn{position:relative;margin-top:14px;width:140px;height:30px}
/* deals */
.deals{top:1633px;height:964px;background:linear-gradient(180deg,#2a0709 0%,#3e0b0e 30%,#170708 60%,#0e0e0e 100%)}
.eyebrow{position:absolute;font-size:11px;color:var(--yellow);font-weight:500;letter-spacing:.5px}
.banner{position:absolute;top:151px;height:239px;border:2px solid #5a1014}
.banner-a{left:124px;width:469px;background:#0a0a0a}
.banner-b{left:609px;width:465px;background:linear-gradient(90deg,#1a0506,#3a0a0c)}
.ticks{position:absolute;left:22px;top:140px;font-size:9px;color:#ddd;line-height:24px}
.ticks div{display:flex;align-items:center;gap:8px}
.count{display:flex;gap:26px;font-size:10px;color:#111;background:var(--yellow);padding:4px 16px}
.count div{text-align:center;line-height:12px}
.count small{display:block;font-size:7px}
.why{left:124px;top:524px;width:950px;height:402px;background:#121212;border:1px solid #3a3a3a}
.why h2{position:absolute;left:48px;top:46px;font-family:var(--display);font-size:28px;line-height:33px;font-weight:400}
.why .p{position:absolute;left:48px;top:144px;width:480px;font-size:9px;line-height:14px;color:#bbb}
.feat{position:absolute;display:flex;gap:14px;width:220px}
.feat .ic{width:26px;height:26px;border-radius:50%;background:var(--red);flex:none}
.feat b{display:block;font-size:14px;font-weight:500;color:var(--yellow)}
.feat small{font-size:9px;color:#aaa}
/* latest */
.latest{top:2597px;height:555px;background:#0e0e0e}
.tabs{position:absolute;left:124px;top:113px;width:280px;height:33px;border:1px solid #666;display:flex;font-size:11px;font-weight:500;padding:2px}
.tabs div{flex:1;display:flex;align-items:center;justify-content:center}
.tabs .on{background:var(--red)}
.pcard{position:absolute;top:178px;width:216px}
.pcard .img{height:220px;background:linear-gradient(160deg,#e9e9e9,#a9a9a9);position:relative}
.pcard .sale{position:absolute;right:14px;top:10px;background:#d8b36a;color:#111;font-size:10px;font-weight:600;padding:2px 10px}
.pcard .st{margin-top:10px;font-size:10px;color:var(--yellow)}
.pcard .st span{color:#aaa}
.pcard h4{margin-top:4px;font-size:13px;font-weight:500;line-height:19px;height:38px}
.pcard .pr{font-size:10px;color:var(--yellow);margin-top:2px}
.pcard .btn{position:relative;margin-top:10px;width:216px;height:30px;font-size:13px}
.pcard.dim{opacity:.3}
/* brands */
.brands{top:3152px;height:934px;background:linear-gradient(180deg,#140506 0%,#3a0a0c 35%,#1c0708 55%,#0e0e0e 100%)}
.bc{position:absolute;top:163px;width:130px;height:130px;border-radius:50%;background:#0a0a0a;border:4px solid #e8e8e8;display:flex;align-items:center;justify-content:center;font-family:var(--display);font-size:14px;color:var(--white);text-align:center}
.arrow{position:absolute;width:24px;height:24px;border-radius:50%;display:flex;align-items:center;justify-content:center}
.ghost{position:absolute;left:0;width:1200px;top:308px;text-align:center;font-family:var(--display);font-size:120px;color:rgba(255,255,255,.06);letter-spacing:8px}
.reviews{left:124px;top:398px;width:950px;height:502px;background:#111;border-top:12px solid var(--yellow);border-left:1px solid #333;border-right:1px solid #333;border-bottom:1px solid #333}
.rv-photo{position:absolute;top:138px;width:203px;height:258px;background:linear-gradient(160deg,#6a6a6a,#2a2a2a)}
.rv-name{position:absolute;top:138px;width:151px;height:56px;background:#1e1e1e;padding:8px 10px;font-size:10px;line-height:13px}
.rv-name small{display:block;font-size:8px;color:#999}
.rv-name .s{color:var(--yellow);font-size:9px}
.rv-text{position:absolute;top:204px;width:151px;height:174px;background:#1e1e1e;padding:16px 12px;font-size:9px;line-height:14px;color:#ccc}
.quote{position:absolute;top:132px;font-family:var(--display);font-size:56px;line-height:56px;color:var(--white)}
/* blogs */
.blogs{top:4086px;height:563px;background:#0e0e0e}
.bcard{position:absolute;top:134px;width:306px}
.bcard .img{height:188px;position:relative}
.bcard .date{background:var(--red);font-size:9px;text-align:center;padding:3px 0}
.bcard h4{margin-top:20px;font-size:14px;color:var(--yellow);font-weight:500;line-height:20px}
.bcard p{margin-top:12px;font-size:9px;line-height:14px;color:#999}
/* join */
.join{top:4649px;height:356px;background:linear-gradient(180deg,#3a0a0c,#241011 50%,#2c1a16)}
.join h2{position:absolute;left:0;width:1200px;top:44px;text-align:center;font-family:var(--display);font-size:30px;font-weight:400}
.join p{position:absolute;left:340px;width:520px;top:94px;text-align:center;font-size:13px;line-height:21px;color:#ddd}
.field{position:absolute;width:297px;height:38px;background:rgba(255,255,255,.28);border:1px solid rgba(255,255,255,.5);font-size:13px;color:#eee;display:flex;align-items:center;padding-left:18px}
/* footer */
.site-footer{top:5005px;height:391px;background:#0a0a0a}
.fcol{position:absolute;top:146px;font-size:9px;line-height:21px;color:#ddd}
.fcol h5{font-size:13px;font-weight:500;color:var(--white);margin-bottom:6px;letter-spacing:.3px}
.soc{display:flex;gap:6px}
.soc span{width:20px;height:20px;border-radius:50%;border:1px solid #aaa}
.copy{position:absolute;left:124px;width:950px;top:356px;border-top:1px solid #333;padding-top:8px;text-align:center;font-size:9px;color:#bbb}
</style>
</head>
<body>

<div class="topbar"><span>‹</span><span>Trusted by <b>1000+ Artists</b></span><span>›</span></div>

<header class="site-header">
  <div class="logo" style="left:124px;top:22px;font-size:22px"><i></i>MARROW ARC</div>
  <nav class="nav"><span>Featured Products ▾</span><span>Promo / Deals</span><span>About Us</span><span>New Arrivals</span><span>Reviews</span><span>Contact</span></nav>
  <div class="icons">
    <span><svg width="12" height="12" viewBox="0 0 12 12"><circle cx="5" cy="5" r="3.5" fill="none" stroke="#fff" stroke-width="1.4"/><line x1="7.6" y1="7.6" x2="11" y2="11" stroke="#fff" stroke-width="1.4"/></svg></span>
    <span><svg width="12" height="12" viewBox="0 0 12 12"><path d="M1 2h2l1.5 6h6l1-4.5H4" fill="none" stroke="#fff" stroke-width="1.2"/><circle cx="5" cy="10.5" r="1" fill="#fff"/><circle cx="9.5" cy="10.5" r="1" fill="#fff"/></svg></span>
    <span><svg width="12" height="12" viewBox="0 0 12 12"><path d="M6 10.5 1.5 6A2.5 2.5 0 0 1 6 3a2.5 2.5 0 0 1 4.5 3Z" fill="none" stroke="#fff" stroke-width="1.2"/></svg></span>
    <span><svg width="12" height="12" viewBox="0 0 12 12"><circle cx="6" cy="4" r="2.3" fill="none" stroke="#fff" stroke-width="1.2"/><path d="M1.8 11a4.2 4.2 0 0 1 8.4 0" fill="none" stroke="#fff" stroke-width="1.2"/></svg></span>
  </div>
</header>

<section class="hero">
  <div class="ph hero-photo" role="img" aria-label="Gloved tattoo artist working with a rotary machine on a client's arm"></div>
  <h1>Premium <span class="y">Tattoo</span><br>Equipment for Artists<br>Who Demand More</h1>
  <p>South Africa's trusted supplier for pro machines, needles, inks &amp; hygiene essentials — built for studios, artists &amp; passionate creators.</p>
  <div class="btn btn-red" style="left:124px;top:403px;width:135px;height:32px">Shop Now</div>
  <div class="btn btn-white" style="left:276px;top:403px;width:180px;height:32px">Request a Quote</div>
</section>

<section class="cats">
  <div class="cat dim" style="left:-44px"><div class="c"><div role="img" aria-label="Piercing tools"></div></div><p>Piercing</p></div>
  <div class="cat" style="left:98px"><div class="c"><div role="img" aria-label="Tattoo machine"></div></div><p>Tattoo Machines</p></div>
  <div class="cat" style="left:255px"><div class="c"><div role="img" aria-label="Tattoo ink bottle"></div></div><p>Tattoo Inks</p></div>
  <div class="cat" style="left:431px"><div class="c"><div role="img" aria-label="Needle cartridge"></div></div><p>Needles &amp; Cartridges</p></div>
  <div class="cat" style="left:607px"><div class="c"><div role="img" aria-label="Power supply accessory"></div></div><p>Accessories</p></div>
  <div class="cat" style="left:764px"><div class="c"><div role="img" aria-label="Studio stool"></div></div><p>Studio Furniture</p></div>
  <div class="cat" style="left:929px"><div class="c"><div role="img" aria-label="Medical supplies box"></div></div><p>Medical Supplies</p></div>
  <div class="cat dim" style="left:1084px"><div class="c"><div role="img" aria-label="Discounted products"></div></div><p>Expired products</p></div>
</section>

<section class="featured">
  <h2 class="h-sec y" style="left:124px;top:42px;color:var(--yellow)">Featured Products</h2>
  <p class="sub" style="left:124px;top:92px">Our most-trusted machines, inks, and essentials — chosen by top South African's artists</p>
  <div class="btn btn-red" style="left:912px;top:80px;width:162px;height:30px;text-transform:none;font-weight:500;font-size:12px">View All Products &nbsp;»</div>
  <div class="fcard" style="left:124px"><div class="img" role="img" aria-label="Ink mixer device with brass shaft"><span class="heart"></span></div><h3>Ink Mixer – Iron Hound Coil Works Machines</h3><p>A reliable, high-speed ink mixer designed for smooth, consistent blending.</p><div class="btn btn-red">Add to Cart</div></div>
  <div class="fcard" style="left:450px"><div class="img" role="img" aria-label="Boxes of liner needle cartridges"><span class="heart"></span></div><h3>KVR Ultra Liners – KVR Ultra Cartridges</h3><p>Precision-engineered liners delivering ultra-smooth, consistent lines for professional results.</p><div class="btn btn-red">Add to Cart</div></div>
  <div class="fcard" style="left:774px"><div class="img" role="img" aria-label="Red tattoo ink bottle"><span class="heart"></span></div><h3>Vantor Ink – Pomegranate 1 Oz – Vantor Tattoo Ink</h3><p>Precision-engineered liners delivering ultra-smooth, consistent lines for professional results.</p><div class="btn btn-red">Add to Cart</div></div>
</section>

<section class="deals">
  <p class="eyebrow" style="left:124px;top:54px">LIMITED-TIME PROMO / DEALS</p>
  <h2 class="h-sec" style="left:124px;top:84px;font-size:30px">Deals &amp; Limited Drops</h2>
  <div class="banner banner-a">
    <div class="abs" style="left:190px;top:6px;font-family:var(--display);font-size:12px">MARROW ARC</div>
    <div class="abs" style="left:22px;top:34px;font-size:9px">Limited Time OFFER</div>
    <div class="abs" style="left:22px;top:50px;font-family:var(--display);font-size:32px;background:#3a0a0c;padding:2px 8px">10<span style="font-size:18px">% OFF</span></div>
    <div class="abs" style="left:22px;top:102px;font-size:20px;font-weight:600">on <span style="color:var(--yellow)">Selected</span> Machines</div>
    <div class="ticks">
      <div><svg width="10" height="10" viewBox="0 0 10 10"><circle cx="5" cy="5" r="4.3" fill="none" stroke="#ddd"/><path d="M3 5l1.5 1.5L7 3.5" fill="none" stroke="#ddd"/></svg>Secure Payments</div>
      <div><svg width="10" height="10" viewBox="0 0 10 10"><circle cx="5" cy="5" r="4.3" fill="none" stroke="#ddd"/><path d="M3 5l1.5 1.5L7 3.5" fill="none" stroke="#ddd"/></svg>Fast Shipping</div>
      <div><svg width="10" height="10" viewBox="0 0 10 10"><circle cx="5" cy="5" r="4.3" fill="none" stroke="#ddd"/><path d="M3 5l1.5 1.5L7 3.5" fill="none" stroke="#ddd"/></svg>Extensive Stock Range</div>
    </div>
    <div class="ph" style="left:250px;top:40px;width:200px;height:180px;background:radial-gradient(circle at 50% 50%,#2f5a3a,#141414 70%)" role="img" aria-label="Coil tattoo machine"></div>
  </div>
  <div class="banner banner-b">
    <div class="abs" style="left:12px;top:6px;font-family:var(--display);font-size:12px">MARROW ARC</div>
    <div class="ph" style="left:0;top:0;width:190px;height:235px;background:linear-gradient(160deg,#5a0e12,#2a0506);clip-path:polygon(0 0,100% 0,70% 100%,0 100%)" role="img" aria-label="Red alarm clock beside an ink bottle"></div>
    <div class="abs" style="left:240px;top:46px;width:200px;text-align:center;font-size:20px;line-height:28px;font-weight:500">Countdown timer<br>for urgency</div>
    <div class="abs" style="left:232px;top:118px;width:216px;background:var(--red);font-size:8px;text-align:center;padding:3px">Create urgency for upcoming sales, releases, and product promos</div>
    <div class="abs count" style="left:232px;top:148px;width:216px"><div>03<small>Days</small></div><div>15<small>Hours</small></div><div>40<small>Minutes</small></div><div>29<small>Seconds</small></div></div>
    <div class="btn btn-red" style="left:296px;top:198px;width:88px;height:20px;font-size:8px">Shop Now</div>
  </div>
  <div class="btn btn-red" style="left:518px;top:428px;width:164px;height:33px;font-size:13px">Shop the Deals</div>

  <div class="abs why">
    <h2>WHY SOUTH AFRICA'S TOP<br>ARTISTS CHOOSE US</h2>
    <p class="p">At Marrow Arc, we're committed to supplying artists and studios with premium equipment they can trust. From top-tier machines and industry-leading cartridges to reliable hygiene essentials, every product is carefully sourced for performance, safety, and consistency.</p>
    <div class="feat" style="left:48px;top:212px"><span class="ic"></span><div><b>Premium Quality Gear</b><small>Trusted global brands</small></div></div>
    <div class="feat" style="left:250px;top:212px"><span class="ic"></span><div><b>Fast Local Shipping</b><small>Nationwide delivery</small></div></div>
    <div class="feat" style="left:48px;top:273px"><span class="ic"></span><div><b>B2B Pricing Available</b><small>Bulk &amp; studio discounts</small></div></div>
    <div class="feat" style="left:250px;top:273px"><span class="ic"></span><div><b>Safe &amp; Certified Products</b><small>Hygiene-approved and compliant</small></div></div>
    <div class="btn btn-red" style="left:48px;top:330px;width:162px;height:33px;font-size:13px">Join With Us</div>
    <div class="ph" style="left:600px;top:17px;width:310px;height:364px;background:linear-gradient(160deg,#9aa6b4,#3c4552 55%,#1e2128)" role="img" aria-label="Artist in black gloves tattooing a client"></div>
    <div class="abs" style="left:548px;top:249px;width:140px;height:140px;border-radius:50%;background:#ececec;border:6px solid #1a1a1a"></div>
  </div>
</section>

<section class="latest">
  <h2 class="h-sec" style="left:124px;top:27px;color:var(--yellow)">Latest Products</h2>
  <p class="sub" style="left:124px;top:72px">Discover the newest arrivals crafted for precision, performance, and next-level artistry.</p>
  <div class="tabs"><div class="on">New Arrivals</div><div>Best Sellers</div></div>
  <div class="btn btn-red" style="left:954px;top:113px;width:120px;height:30px;text-transform:none;font-size:12px;font-weight:500">View All &nbsp;»</div>
  <div class="pcard dim" style="left:-136px"><div class="img" role="img" aria-label="Aftercare product"></div><div class="st">★★★★★ <span>(134)</span></div><h4>Brisk Tallow Aftercare</h4><p class="pr">$22.00</p><div class="btn btn-red">Shop Now</div></div>
  <div class="pcard" style="left:113px"><div class="img" role="img" aria-label="Aftercare ointment sachets"><span class="sale">SALE</span></div><div class="st">★★★★★ <span>(134)</span></div><h4>MELTRA Tattoo Aftercare Ointment 5 g Sachet</h4><p class="pr">$22.00</p><div class="btn btn-red">Shop Now</div></div>
  <div class="pcard" style="left:359px"><div class="img" role="img" aria-label="UV steriliser cabinet"><span class="sale">SALE</span></div><div class="st">★★★★★ <span>(134)</span></div><h4>UV Cabinet Large for Tattoo Tools</h4><p class="pr">$22.00</p><div class="btn btn-red">Shop Now</div></div>
  <div class="pcard" style="left:605px"><div class="img" role="img" aria-label="Small sterilising cabinet"><span class="sale">SALE</span></div><div class="st">★★★★★ <span>(134)</span></div><h4>UV Sterilising Cabinet for Tattoo Tools</h4><p class="pr">$22.00</p><div class="btn btn-red">Shop Now</div></div>
  <div class="pcard" style="left:850px"><div class="img" role="img" aria-label="Box of compostable machine sleeves"><span class="sale">SALE</span></div><div class="st">★★★★★ <span>(134)</span></div><h4>Elite Compostable Pen Machine Sleeves (100 pcs)</h4><p class="pr">$22.00</p><div class="btn btn-red">Shop Now</div></div>
  <div class="pcard dim" style="left:1097px"><div class="img" role="img" aria-label="Cleansing spray bottle"></div><div class="st">★★★★★ <span>(134)</span></div><h4>Clean Foam Spray – 50 ml</h4><p class="pr">$22.00</p><div class="btn btn-red">Shop Now</div></div>
</section>

<section class="brands">
  <h2 class="h-sec" style="left:0;width:1200px;text-align:center;top:58px;color:var(--yellow)">Brand Showcase</h2>
  <p class="sub" style="left:0;width:1200px;text-align:center;top:112px;color:#ddd">Trusted Global Brands Preferred by Professional Artists Worldwide.</p>
  <div class="arrow" style="left:101px;top:216px;border:1px solid #ccc">‹</div>
  <div class="bc" style="left:147px">Grim Quill</div>
  <div class="bc" style="left:299px">Ember Coil</div>
  <div class="bc" style="left:454px">Vivenza</div>
  <div class="bc" style="left:607px">Vantor</div>
  <div class="bc" style="left:762px">Everline</div>
  <div class="bc" style="left:917px">Regent</div>
  <div class="arrow" style="left:1075px;top:216px;border:1px solid #ccc">›</div>
  <div class="ghost">MARROW ARC</div>

  <div class="abs reviews">
    <p class="abs" style="left:0;width:948px;text-align:center;top:52px;font-size:13px;color:var(--yellow)">What Our Customers Say</p>
    <h2 class="abs" style="left:0;width:948px;text-align:center;top:80px;font-family:var(--display);font-size:30px;font-weight:400">REAL FEEDBACK <span style="color:#555">REAL RESULT</span></h2>
    <div class="rv-photo" style="left:53px" role="img" aria-label="Customer portrait in white shirt"></div>
    <div class="quote" style="left:56px">“</div>
    <div class="rv-name" style="left:273px">Dylan K., Cape Town<small>Studio Owner</small><span class="s">★★★★★</span></div>
    <div class="rv-text" style="left:273px">"Marrow Arc never disappoints. The quality of their machines and cartridges is top-notch, and delivery is always fast. My studio relies on their products daily — absolutely trustworthy supplier."</div>
    <div class="rv-photo" style="left:507px" role="img" aria-label="Customer portrait in white vest"></div>
    <div class="quote" style="left:668px">”</div>
    <div class="rv-name" style="left:727px">Mireille S., Durban<small>Professional Artist</small><span class="s">★★★★★</span></div>
    <div class="rv-text" style="left:727px">"I've ordered inks, needles, and hygiene supplies multiple times, and everything arrives well-packaged and exactly as expected. Great prices, great service, and gear that performs every time."</div>
    <div class="btn btn-red" style="left:367px;top:446px;width:216px;height:30px;font-size:13px">View All Reviews</div>
    <div class="arrow" style="left:800px;top:442px;width:34px;height:34px;background:#555">‹</div>
    <div class="arrow" style="left:846px;top:442px;width:34px;height:34px;background:var(--red)">›</div>
  </div>
</section>

<section class="blogs">
  <h2 class="h-sec" style="left:124px;top:36px">Latest <span class="y">Blogs / Articles</span></h2>
  <p class="sub" style="left:124px;top:84px">Discover the newest arrivals crafted for precision, performance, and next-level artistry.</p>
  <div class="bcard" style="left:124px"><div class="img" style="background:linear-gradient(160deg,#c9806a,#7a2a20)" role="img" aria-label="Healing tattoo on skin"></div><div class="date">Friday, October, 13, 2025</div><h4>When Tattoos Heal the Wrong Way | Marrow Arc South Africa</h4><p>I have been tattooing long enough to know that not every piece settles the way you want it to...</p></div>
  <div class="bcard" style="left:447px"><div class="img" style="background:#000;display:flex;align-items:center;justify-content:center;font-family:var(--display);font-size:40px;line-height:44px;text-align:center">STARK<br>PIGMENT</div><div class="date">Monday, September, 05, 2025</div><h4>Stark Pigment: The Epitome of Tattoo Ink Excellence</h4><p>When it comes to tattooing, there is no room for compromise. The quality of the ink used plays a pivotal role...</p></div>
  <div class="bcard" style="left:769px"><div class="img" style="background:linear-gradient(160deg,#3a2a2c,#141414)" role="img" aria-label="Row of ink bottles"></div><div class="date">Wednesday, October, 11, 2025</div><h4>Discover Parable Pigment: Professional-Grade Organic Tattoo Ink</h4><p>In the ever-evolving world of tattoo artistry, staying at the forefront requires the use of high-quality products that...</p></div>
  <div class="btn btn-red" style="left:513px;top:496px;width:174px;height:30px;font-size:13px">View All Blogs</div>
</section>

<section class="join">
  <h2>JOIN THE MARROW ARC CREW</h2>
  <p>Stay updated with new product drops, exclusive deals, artist tips, and studio essentials — straight to your inbox.</p>
  <div class="field" style="left:281px;top:144px">First Name</div>
  <div class="field" style="left:622px;top:144px">Last Name</div>
  <div class="field" style="left:281px;top:207px">Phone Number</div>
  <div class="field" style="left:622px;top:207px">Email ID</div>
  <div class="btn btn-red" style="left:521px;top:278px;width:157px;height:32px;font-size:13px">Subscribe</div>
</section>

<footer class="site-footer">
  <div class="logo" style="left:0;width:1200px;justify-content:center;top:60px;font-size:28px"><i></i>MARROW ARC</div>
  <div class="fcol" style="left:124px"><h5>INFORMATION</h5>Track My Parcel<br>Delivery Information<br>About Us<br>Privacy Policy (POPI)<br>Terms &amp; Conditions<br>Original Manufacturers Guarantee<br>Cookies Policy<br>Returns &amp; Refunds Policy</div>
  <div class="fcol" style="left:356px"><h5>CUSTOMER SERVICE</h5>Contact Us<br>Returns<br>Site Map</div>
  <div class="fcol" style="left:614px"><h5>CONTACT INFO</h5>
    <div style="display:flex;align-items:center;gap:8px"><svg width="20" height="20" viewBox="0 0 20 20"><circle cx="10" cy="10" r="9" fill="none" stroke="#aaa"/><path d="M7 6l2 2-1 1.5a6 6 0 0 0 2.5 2.5L12 11l2 2-1.5 1.5C9 14 6 11 5.5 7.5Z" fill="#ddd"/></svg>082 555 0147</div>
    <div style="display:flex;align-items:center;gap:8px;margin-top:10px"><svg width="20" height="20" viewBox="0 0 20 20"><circle cx="10" cy="10" r="9" fill="none" stroke="#aaa"/><rect x="5.5" y="7" width="9" height="6" fill="none" stroke="#ddd"/><path d="M5.5 7l4.5 3.5L14.5 7" fill="none" stroke="#ddd"/></svg><span style="color:var(--red)">hello@marrowarc.co.za</span></div>
  </div>
  <div class="fcol" style="left:806px"><h5>SOCIAL MEDIA</h5><div class="soc"><span></span><span></span><span></span><span></span></div></div>
  <div class="fcol" style="left:976px"><h5>MY ACCOUNT</h5>Order History<br>Wish List<br>Specials<br>Newsletter</div>
  <div class="copy">© Marrow Arc Pty Ltd © 2025</div>
</footer>

</body>
</html>
```